Laser Tattoo Removal Business Cards

We are looking for a professional business card design for a laser tattoo removal business. Ideally looking for a black business card design. The name of the business is Brightline Tattoo Removal. We place our cards at local tattoo shops so we ideally are looking for something trendy/edgy to draw both male and female clientele in.

Target Market(s)

Male/Female ages 18-60

Contact Information for Business Card

black background ideally.. hoping to stay within greys, whites and black

Font styles to use
Serif
Sans Serif

Colors
121212
a9a9a9
5c5c5c
f5f5f5
ffffff
7f7f7f
606060
848484
9d9d9d

Requirements
Must have
• Employee Info:
• Melissa Thornbury
• Chief Executive Offer
• m: 919.537.2846
• w: 919.362.4178
• f: 919.685.3907
• mthornbury@brightlinetattooremoval.example
• Address:
• 4615 Oakmere Pkwy, Suite 210
• Raleigh, NC 27654
• Website:
• www.brightlinetattooremoval.example
Nice to have
• Myabe business name on back or logo on back and employee info on the front

```html
<!DOCTYPE html>
<html lang="en">
<head>
<meta charset="utf-8">
<title>Brightline Tattoo Removal – Business Card</title>
<link rel="stylesheet" href="https://fonts.googleapis.com/css2?family=Questrial&family=Arimo:wght@400&display=swap">
<style>
  :root {
    --ink: #121212;
    --charcoal: #1c1c1c;
    --silver-light: #f5f5f5;
    --silver: #d9d9d9;
    --silver-mid: #a9a9a9;
    --grey: #7f7f7f;
    --grey-dark: #5c5c5c;
    --text-light: #e6e6e6;
    --text-soft: #9d9d9d;
    --stage: #e9e9e9;
  }
  * { box-sizing: border-box; margin: 0; padding: 0; }
  html, body { width: 1200px; height: 969px; overflow: hidden; }
  body {
    background: var(--stage);
    position: relative;
    font-family: "Arimo", Arial, sans-serif;
  }
  .business-card {
    position: absolute;
    left: 100px;
    top: 198px;
    width: 1000px;
    height: 572px;
    border-radius: 8px;
    overflow: hidden;
    background: linear-gradient(180deg, var(--silver-light) 0%, var(--silver) 60%, var(--silver-mid) 100%);
    box-shadow: 0 10px 30px rgba(0,0,0,.18);
  }
  .card-shapes { position: absolute; inset: 0; width: 100%; height: 100%; }
  .brand {
    position: absolute;
    left: 0; right: 0;
    text-align: center;
    font-family: "Questrial", Arial, sans-serif;
    color: var(--ink);
  }
  .brand-name { top: 78px; font-size: 74px; letter-spacing: 6px; line-height: 1; }
  .brand-tagline {
    top: 236px;
    font-size: 30px;
    letter-spacing: 6px;
    display: flex; justify-content: center; align-items: center; gap: 18px;
  }
  .brand-tagline::before, .brand-tagline::after {
    content: ""; width: 26px; height: 2px; background: var(--ink);
  }
  .employee-name {
    position: absolute; left: 0; right: 0; top: 336px;
    text-align: center;
    font-family: "Questrial", Arial, sans-serif;
    font-size: 34px; letter-spacing: 1px;
    color: var(--text-light);
  }
  .employee-title {
    position: absolute; left: 0; right: 0; top: 376px;
    text-align: center; font-size: 23px; color: var(--text-soft);
  }
  .title-rule {
    position: absolute; left: 90px; right: 90px; top: 409px;
    height: 1px; background: var(--grey-dark);
  }
  .contact-row {
    position: absolute; left: 0; right: 0;
    display: flex; justify-content: center; align-items: center; gap: 22px;
    font-size: 22px; color: var(--text-light);
  }
  .phones { top: 428px; }
  .online { top: 466px; font-size: 19px; }
  .address { top: 507px; color: var(--text-soft); font-size: 22px; }
  .contact-item { display: flex; align-items: center; gap: 8px; white-space: nowrap; }
  .contact-icon { width: 20px; height: 20px; fill: var(--silver-mid); flex: none; }
</style>
</head>
<body>
  <section class="business-card" aria-label="Brightline Tattoo Removal business card">
    <svg class="card-shapes" viewBox="0 0 1000 572" preserveAspectRatio="none" aria-hidden="true">
      <defs>
        <linearGradient id="silverBand" x1="0" y1="0" x2="1" y2="0">
          <stop offset="0" stop-color="#7f7f7f"/>
          <stop offset=".5" stop-color="#f5f5f5"/>
          <stop offset="1" stop-color="#7f7f7f"/>
        </linearGradient>
        <linearGradient id="blackPanel" x1="0" y1="0" x2="0" y2="1">
          <stop offset="0" stop-color="#121212"/>
          <stop offset="1" stop-color="#262626"/>
        </linearGradient>
      </defs>
      <path d="M0,188 Q500,398 1000,188 L1000,572 L0,572 Z" fill="url(#silverBand)"/>
      <path d="M0,207 Q500,413 1000,207 L1000,572 L0,572 Z" fill="url(#blackPanel)"/>
    </svg>

    <div class="brand brand-name">BRIGHTLINE</div>
    <div class="brand brand-tagline">TATTOO REMOVAL</div>

    <h1 class="employee-name">MELISSA THORNBURY</h1>
    <p class="employee-title">Chief Executive Offer</p>
    <div class="title-rule"></div>

    <div class="contact-row phones">
      <span class="contact-item">
        <svg class="contact-icon" viewBox="0 0 24 24"><path d="M6.6 10.8a15.2 15.2 0 0 0 6.6 6.6l2.2-2.2a1 1 0 0 1 1-.25 11.4 11.4 0 0 0 3.6.6 1 1 0 0 1 1 1V20a1 1 0 0 1-1 1A17 17 0 0 1 3 4a1 1 0 0 1 1-1h3.5a1 1 0 0 1 1 1c0 1.25.2 2.45.6 3.6a1 1 0 0 1-.25 1z"/></svg>
        919.362.4178
      </span>
      <span class="contact-item">
        <svg class="contact-icon" viewBox="0 0 24 24"><path d="M7 1h10a2 2 0 0 1 2 2v18a2 2 0 0 1-2 2H7a2 2 0 0 1-2-2V3a2 2 0 0 1 2-2zm0 3v14h10V4zm5 15.5a1 1 0 1 0 0 2 1 1 0 0 0 0-2z"/></svg>
        919.537.2846
      </span>
      <span class="contact-item">
        <svg class="contact-icon" viewBox="0 0 24 24"><path d="M6 3h12v5H6zM4 9h16a2 2 0 0 1 2 2v6h-4v4H6v-4H2v-6a2 2 0 0 1 2-2zm4 7v3h8v-3z"/></svg>
        919.685.3907
      </span>
    </div>

    <div class="contact-row online">
      <span class="contact-item">
        <svg class="contact-icon" viewBox="0 0 24 24"><path d="M2 5h20v14H2zm2 2v.5l8 5 8-5V7l-8 5z"/></svg>
        mthornbury@brightlinetattooremoval.example
      </span>
      <span class="contact-item">
        <svg class="contact-icon" viewBox="0 0 24 24"><path d="M12 2a10 10 0 1 0 0 20 10 10 0 0 0 0-20zm-1 17.9A8 8 0 0 1 4.1 11L9 16v1a2 2 0 0 0 2 2zm6.9-2.5A2 2 0 0 0 16 16h-1v-3a1 1 0 0 0-1-1H8v-2h2a1 1 0 0 0 1-1V7h2a2 2 0 0 0 2-2v-.4a8 8 0 0 1 2.9 12.8z"/></svg>
        www.brightlinetattooremoval.example
      </span>
    </div>

    <p class="contact-row address">4615 Oakmere Pkwy, Suite 210, Raleigh, NC 27654</p>
  </section>
</body>
</html>
```